Business card design for a dynamic IT consulting company

We need a business card design for a young firm, specialized in the Telecommunications/Consulting industry. The name of the company is Quindor and Partners Business Consulting Ltd. (Short name: Quindor and Partnes)
Quindor = solve read reverse, so we aim to be uncomplicated and solution-oriented. The small pipe in our logo is also related to the word solve. So we need a new business card design, which is simple, eye catching and something non traditional (I would probably prefer a square shaped design rather than a rectangle, but open for suggestions). Attached our logo.

Target Market(s)

Usually our customers are Tier1 Telecoms providers (Q-Netra, Palorix, etc) and their executives.

Industry/Entity Type

Business

Contact Information for Business Card

Name: Bence Tolnavari
Email: b.tolnavari@quindor.hu
Web: www.quindor.hu
Mobile: +36 30 518 2769
Title: Managing Director

Optional:
Company name: Quindor and Partners Ltd.
Address: 1087 Budapest, Tolvenka str. 28/C, Hungary

Font styles to use
Other font styles liked:
• helveticaneue_medium, Prime Regular are used now.

Colors

Designer to choose colors to be used in the design.

Requirements
Must have
• I would like to have a 2 sided design.
Nice to have
• I thought if we make the logo a bit bigger (without the company name), that could go to the back with the company name below. I though, if the pipe in the logo is somehow touchable on the business card, would be nice and unique.

```html
<!DOCTYPE html>
<html lang="en">
<head>
<meta charset="utf-8">
<title>Quindor &amp; Partners — Business Card</title>
<link rel="stylesheet" href="https://fonts.googleapis.com/css2?family=Exo+2:wght@400&family=Montserrat:wght@400;500&display=swap">
<style>
  :root {
    --backdrop: #161616;
    --card: #242424;
    --card-edge: #2c2c2c;
    --accent-blue: #1b9be0;
    --accent-magenta: #b8378f;
    --ink: #f2f2f2;
  }
  * { box-sizing: border-box; margin: 0; padding: 0; }
  html, body {
    width: 1200px; height: 900px; overflow: hidden;
    background: radial-gradient(ellipse at 60% 40%, #262626 0%, var(--backdrop) 70%);
    font-family: "Montserrat", Arial, sans-serif;
    color: var(--ink);
  }
  .card {
    position: absolute;
    left: 250px;
    width: 700px; height: 400px;
    background: linear-gradient(135deg, var(--card) 0%, var(--card-edge) 100%);
    box-shadow: 0 12px 30px rgba(0,0,0,.55);
  }
  .card::after {
    content: ""; position: absolute; left: 0; right: 0; bottom: 0;
    height: 7px; background: var(--accent-blue);
  }
  .card--front { top: 40px; }
  .card--back { top: 470px; }

  .brand {
    position: absolute; left: 0; right: 0; top: 170px;
    display: flex; justify-content: center; align-items: center; gap: 14px;
  }
  .brand__mark { width: 22px; height: 22px; background: var(--accent-magenta); }
  .brand__name { font-size: 42px; font-weight: 500; color: var(--ink); letter-spacing: .5px; }

  .person {
    position: absolute; right: 380px; top: 150px; text-align: right;
  }
  .person__name {
    font-family: "Exo 2", Arial, sans-serif;
    font-size: 30px; color: var(--accent-blue); letter-spacing: 1px; white-space: nowrap;
  }
  .person__title { font-size: 18px; margin-top: 6px; letter-spacing: .5px; }

  .divider {
    position: absolute; left: 345px; top: 168px;
    width: 2px; height: 72px; background: var(--accent-magenta);
  }

  .contacts { position: absolute; left: 380px; top: 170px; list-style: none; }
  .contacts li {
    display: flex; align-items: center; gap: 14px;
    font-size: 17px; letter-spacing: .6px; height: 26px;
  }
  .contacts svg { width: 16px; height: 16px; fill: none; stroke: var(--accent-blue); stroke-width: 1.6; }
  .contacts .icon-fill { fill: var(--accent-blue); stroke: none; }
</style>
</head>
<body>
  <section class="card card--front" aria-label="Card front">
    <div class="brand">
      <span class="brand__mark"></span>
      <span class="brand__name">Quindor &amp; Partners</span>
    </div>
  </section>

  <section class="card card--back" aria-label="Card back">
    <div class="person">
      <p class="person__name">BENCE TOLNAVARI</p>
      <p class="person__title">Managing Director</p>
    </div>
    <div class="divider"></div>
    <ul class="contacts">
      <li>
        <svg viewBox="0 0 16 16" aria-hidden="true"><path class="icon-fill" d="M3 1l3 3-1.5 2a9 9 0 0 0 5.5 5.5L12 10l3 3-2 2C7 15 1 9 1 3z"/></svg>
        +36 30 518 2769
      </li>
      <li>
        <svg viewBox="0 0 16 16" aria-hidden="true"><rect class="icon-fill" x="1" y="3" width="14" height="10"/><path d="M1 3l7 6 7-6" stroke="#242424"/></svg>
        b.tolnavari@quindor.hu
      </li>
      <li>
        <svg viewBox="0 0 16 16" aria-hidden="true"><circle cx="8" cy="8" r="6.5"/><ellipse cx="8" cy="8" rx="3" ry="6.5"/><path d="M1.5 8h13M2.5 5h11M2.5 11h11"/></svg>
        www.quindor.hu
      </li>
    </ul>
  </section>
</body>
</html>
```